Wine Label Design Tessway Crest Red Wine

Design for new wine brand "Tessway Crest". Thinking more of an upscale nautical vibe, or something more classic- old school chateau like.
Red Blend or Cabernet
2018 California
Back label copy:
Tessway Crest encapsulates all the wonder of Bridlen Cove on a perfect New England summer day. With one sip, you’ll be transported to the pavilions and boardwalks as you get ready to tighten your sails and head out on the Sound. So pull up a chair and pour a glass as you enjoy the warmth of summer in a glass any time you indulge in this wine.

```html
<!DOCTYPE html>
<html lang="en">
<head>
<meta charset="utf-8">
<title>Tessway Crest Red Blend Label</title>
<link rel="stylesheet" href="https://fonts.googleapis.com/css2?family=Rye&family=Libre+Baskerville&display=swap">
<style>
  :root {
    --backdrop: #bdbdbd;
    --label-light: #e6e6e6;
    --label-mid: #d2d2d2;
    --wine-deep: #4e1d22;
    --wine-soft: #7a4a4f;
    --lighthouse-pink: #c06a9a;
    --gold: #d9b24c;
    --gold-light: #f3d889;
    --brand-blue: #3f6fa6;
    --band-red: #8e1f22;
    --band-dark: #5c1114;
    --ink: #2a2a2a;
  }
  html, body {
    margin: 0;
    padding: 0;
    width: 900px;
    height: 1200px;
    overflow: hidden;
    background: var(--backdrop);
  }
  .canvas {
    position: relative;
    width: 900px;
    height: 1200px;
  }
  .label {
    position: absolute;
    left: 90px;
    top: 65px;
    width: 720px;
    height: 1070px;
    background: linear-gradient(180deg, var(--label-light) 0%, var(--label-mid) 100%);
    box-shadow: 0 2px 6px rgba(0,0,0,0.15);
  }
  .emblem {
    position: absolute;
    left: 158px;
    top: 115px;
    width: 404px;
    height: 404px;
  }
  .brand-name {
    position: absolute;
    left: 0;
    top: 590px;
    width: 100%;
    text-align: center;
    margin: 0;
    font-family: "Rye", serif;
    font-weight: 400;
    font-size: 74px;
    line-height: 1;
    color: var(--brand-blue);
    letter-spacing: 1px;
  }
  .varietal-bar {
    position: absolute;
    left: 0;
    top: 767px;
    width: 100%;
    height: 32px;
    background: linear-gradient(180deg, var(--gold-light), var(--gold));
    display: flex;
    align-items: center;
    justify-content: center;
  }
  .varietal-bar span {
    font-family: "Libre Baskerville", serif;
    font-size: 26px;
    color: var(--ink);
  }
  .vintage-band {
    position: absolute;
    left: 0;
    top: 895px;
    width: 100%;
    height: 103px;
    box-sizing: border-box;
    border-top: 4px solid var(--gold);
    border-bottom: 4px solid var(--gold);
    background: linear-gradient(180deg, var(--band-red), var(--band-dark));
  }
  .vintage-band .ornament {
    position: absolute;
    top: 30px;
    width: 90px;
    height: 36px;
    border-radius: 18px;
    background: rgba(30, 5, 6, 0.55);
  }
  .ornament.left { left: 18px; }
  .ornament.right { right: 18px; }
  .vintage-band .vintage-frame {
    position: absolute;
    left: 140px;
    right: 140px;
    top: 4px;
    bottom: 4px;
    border-left: 1px solid rgba(30,5,6,0.7);
    border-right: 1px solid rgba(30,5,6,0.7);
    border-radius: 40px;
    display: flex;
    align-items: center;
    justify-content: center;
  }
  .vintage-frame span {
    font-family: "Libre Baskerville", serif;
    font-size: 30px;
    color: var(--gold-light);
  }
</style>
</head>
<body>
<div class="canvas">
  <div class="label">
    <svg class="emblem" viewBox="0 0 404 404">
      <defs>
        <linearGradient id="emblemFill" x1="0" y1="1" x2="1" y2="0">
          <stop offset="0" stop-color="var(--wine-deep)"/>
          <stop offset="1" stop-color="var(--wine-soft)"/>
        </linearGradient>
      </defs>
      <polygon points="202,0 404,202 202,404 0,202" fill="var(--gold)"/>
      <polygon points="202,5 399,202 202,399 5,202" fill="url(#emblemFill)" role="img" aria-label="Etched lighthouse illustration in pink on a deep wine ground"/>
    </svg>

    <h1 class="brand-name">Tessway Crest</h1>

    <div class="varietal-bar"><span>Red Blend</span></div>

    <div class="vintage-band">
      <div class="ornament left" role="img" aria-label="Scroll ornament"></div>
      <div class="vintage-frame"><span>2018 California</span></div>
      <div class="ornament right" role="img" aria-label="Scroll ornament"></div>
    </div>
  </div>
</div>
</body>
</html>
```